RK Donnelly & Associates

Create a website encompassing design work already carried out for business card.
Small accounting practice, business accounting and management, superannuation, audit, taxation.

```html
<!DOCTYPE html>
<html lang="en">
<head>
<meta charset="utf-8">
<title>RK Donnelly &amp; Associates</title>
<link href="https://fonts.googleapis.com/css2?family=Open+Sans:ital,wght@0,400;0,600;0,700;1,400&family=Raleway:wght@800&family=Lora:ital@1&display=swap" rel="stylesheet">
<style>
:root{
  --dark:#1c1c1c;
  --blue:#6ba5dc;
  --blue-deep:#5a95cf;
  --text:#333;
  --muted:#7a7a7a;
  --line:#e2e2e2;
  --band:#f4f4f4;
  --white:#fff;
}
*{margin:0;padding:0;box-sizing:border-box}
html,body{width:1200px;height:2314px;overflow:hidden}
body{position:relative;background:var(--white);font-family:"Open Sans",Arial,sans-serif;color:var(--text)}
.abs{position:absolute}

.site-header{left:0;top:0;width:1200px;height:119px;background:var(--dark)}
.brand{left:0;width:1200px;top:38px;text-align:center;color:var(--white);font-size:28px;font-weight:600;display:flex;justify-content:center;align-items:center;gap:14px}
.brand-mark{width:26px;height:26px;background:var(--blue)}
.tagline-bar{left:0;top:119px;width:1200px;height:31px;background:var(--blue);color:var(--white);font-size:11px;font-weight:700;text-align:center;line-height:31px}

.hero{left:0;top:150px;width:1200px;height:615px;background:linear-gradient(90deg,#dfe5ea 0%,#c9d2db 35%,#eef0f2 60%,#d8dde2 100%)}
.hero-title{left:130px;top:385px;font-family:"Raleway",sans-serif;font-weight:800;font-size:62px;color:var(--white);line-height:82px}
.hero-title .amp{color:var(--blue)}
.hero-title .second{display:block;padding-left:141px}
.hero-arrow{top:418px;width:80px;height:80px;border-radius:50%;background:rgba(120,120,120,.55)}
.hero-arrow.prev{left:19px}.hero-arrow.next{left:1103px}
.hero-arrow svg{width:80px;height:80px}

.main-nav{left:0;top:765px;width:1200px;height:63px;background:var(--blue);border-bottom:3px solid var(--blue-deep)}
.main-nav ul{list-style:none;display:flex;position:absolute;left:131px;top:0;height:60px}
.main-nav li{color:var(--white);font-size:13px;line-height:60px;text-align:center;border-right:1px solid rgba(255,255,255,.25)}
.main-nav li.active{background:var(--dark)}

.section-title{font-size:24px;font-weight:600;color:#111;text-transform:uppercase}
.services-title{left:131px;top:868px}
.service{width:450px}
.service-icon{position:absolute;left:0;top:0;width:96px;height:96px;border-radius:50%;background:var(--dark);border:3px solid #555}
.service-icon svg{width:90px;height:90px}
.service h3{position:absolute;left:120px;top:-12px;color:var(--blue);font-size:23px;font-weight:600}
.service .lead{position:absolute;left:120px;top:26px;width:320px;font-size:13px;font-weight:700;line-height:21px}
.service .body{position:absolute;left:0;top:110px;width:470px;font-size:11.5px;color:var(--muted);line-height:20.5px}
.s1{left:131px;top:927px}.s2{left:619px;top:927px}
.s3{left:131px;top:1150px}.s4{left:619px;top:1150px}
.btn-more{left:131px;top:1382px;width:144px;height:54px;background:var(--blue);border-bottom:3px solid var(--blue-deep);color:var(--white);font-size:15px;font-weight:600;text-align:center;line-height:51px}
.divider{left:0;top:1465px;width:1200px;height:1px;background:var(--line)}

.news-title{left:133px;top:1504px}
.about-title{left:762px;top:1504px}
.news-date{left:131px;width:65px;height:55px;background:var(--blue);color:var(--white);text-align:center;font-weight:700}
.news-date b{display:block;font-size:20px;line-height:26px;padding-top:4px}
.news-date span{font-size:12px}
.news-head{left:210px;font-family:"Lora",serif;font-style:italic;font-size:14px;color:#555}
.news-by{left:210px;font-family:"Lora",serif;font-style:italic;font-weight:700;font-size:12px;color:#222}
.news-photo{left:131px;width:107px;height:93px}
.news-text{left:258px;width:440px;font-size:11.5px;line-height:20.5px;color:#444}
.news-sep{left:131px;top:1755px;width:571px;height:1px;background:var(--line)}
.about-text{left:762px;top:1558px;width:305px;font-size:11.5px;line-height:20.5px;color:#444}
.gallery-title{left:762px;top:1697px}
.gallery{left:762px;top:1743px;width:305px;height:219px;display:grid;grid-template-columns:1fr 1fr 1fr;grid-template-rows:1fr 1fr 1fr;gap:3px}
.gallery div{background:linear-gradient(135deg,#9fb2c4,#4b627a)}
.gallery .wide{grid-column:1/3;grid-row:2/4;background:linear-gradient(180deg,#d9dee3,#8e9aa5)}

.newsletter{left:0;top:2013px;width:1200px;height:89px;background:var(--band)}
.newsletter p{position:absolute;left:121px;top:30px;font-size:19px;color:#888;text-transform:uppercase;letter-spacing:.3px}
.newsletter p em{font-style:normal;color:var(--blue)}
.newsletter .field{position:absolute;left:680px;top:22px;width:265px;height:45px;background:var(--white);border:1px solid #ddd;font-size:13px;color:#999;padding:13px 10px}
.newsletter .subscribe{position:absolute;left:956px;top:22px;width:127px;height:45px;background:var(--blue);color:var(--white);font-size:14px;font-weight:600;text-align:center;line-height:45px}

.site-footer{left:0;top:2102px;width:1200px;height:212px;background:var(--dark);color:var(--white)}
.foot-brand{left:133px;top:34px;font-size:16px;font-weight:600;display:flex;gap:10px;align-items:center}
.foot-brand i{width:20px;height:20px;background:var(--blue);display:block}
.socials{left:133px;top:100px;display:flex;gap:11px}
.socials span{width:36px;height:36px;border:2px solid var(--white);border-radius:50%}
.copy{left:131px;top:163px;font-size:11px;color:#aaa}
.foot-col h4{font-size:14px;font-weight:400;letter-spacing:.5px}
.foot-col .rule{width:210px;height:1px;background:#444;margin-top:18px}
.col-posts{left:398px;top:48px}
.col-posts p{font-size:11px;line-height:18px;margin-top:14px;width:215px;color:#ddd}
.col-posts .ago{color:var(--blue);margin-top:10px}
.col-posts .rule.bottom{margin-top:14px}
.col-support{left:687px;top:48px}
.col-support .phone{font-size:22px;font-weight:700;color:var(--blue);margin-top:16px}
.col-support p{font-size:11px;margin-top:6px;color:#ddd}
.col-support p b{color:var(--white);font-weight:700}
.col-support .rule{margin-top:38px}
.col-links{left:984px;top:48px}
.col-links ul{list-style:none;margin-top:14px;font-size:11.5px;line-height:20px;padding-left:8px}
</style>
</head>
<body>

<header class="site-header abs">
  <div class="brand abs"><span class="brand-mark"></span>RK Donnelly &amp; Associates</div>
</header>
<div class="tagline-bar abs">Accountant · Business Solutions · Management · Superannuation · Audit</div>

<section class="hero abs" role="img" aria-label="Photo of a smiling businesswoman with arms crossed in a bright office, colleagues blurred behind her"></section>
<h1 class="hero-title abs">RK DONNELLY <span class="amp">&amp;</span><span class="second">ASSOCIATES</span></h1>
<div class="hero-arrow prev abs"><svg viewBox="0 0 80 80"><path d="M46 22 L30 40 L46 58" fill="none" stroke="#fff" stroke-width="2"/></svg></div>
<div class="hero-arrow next abs"><svg viewBox="0 0 80 80"><path d="M34 22 L50 40 L34 58" fill="none" stroke="#fff" stroke-width="2"/></svg></div>

<nav class="main-nav abs">
  <ul>
    <li class="active" style="width:100px">HOME</li>
    <li style="width:152px">ABOUT US</li>
    <li style="width:132px">PROJECTS</li>
    <li style="width:132px">SERVICES</li>
    <li style="width:164px">NEWS &amp; EVENTS</li>
    <li style="width:125px">BLOG</li>
    <li style="width:140px">CONTACTS</li>
  </ul>
</nav>

<h2 class="section-title services-title abs">Our Services</h2>

<article class="service s1 abs">
  <div class="service-icon"><svg viewBox="0 0 90 90"><path d="M27 44 Q45 20 63 44 Q58 40 54 44 Q50 40 45 44 Q40 40 36 44 Q32 40 27 44Z" fill="#fff"/><path d="M45 44 V58 Q45 62 41 62 Q38 62 38 59" fill="none" stroke="#fff" stroke-width="2.5"/></svg></div>
  <h3>Accounting Practice</h3>
  <p class="lead">Lorem ipsuLorem ipsum dolor sit amet conse ct etur adipisicing elit, sed dom dolor.</p>
  <p class="body">Lorem ipsum dolor sit amet conse ctetur adipisicing elit, sed do eiusmod tempor incididunt ut labore et dolore magna aliqua. Ut enim ad minim venialkorwem, quis nostrud exercitation ullamco laboris nisi ut aliquip s nisi ut aliquip exea cojmm odo consequat. Duis aute irure dolor...</p>
</article>
<article class="service s2 abs">
  <div class="service-icon"><svg viewBox="0 0 90 90"><path d="M38 28 H52 L48 36 Q62 44 60 58 Q58 64 45 64 Q32 64 30 58 Q28 44 42 36Z" fill="#fff"/><text x="45" y="57" font-size="14" font-weight="700" text-anchor="middle" fill="#1c1c1c">$</text></svg></div>
  <h3>Business Accounting</h3>
  <p class="lead">Lorem ipsuLorem ipsum dolor sit amet conse ct etur adipisicing elit, sed dom dolor.</p>
  <p class="body">Lorem ipsum dolor sit amet conse ctetur adipisicing elit, sed do eiusmod tempor incididunt ut labore et dolore magna aliqua. Ut enim ad minim venialkorwem, quis nostrud exercitation ullamco laboris nisi ut aliquip s nisi ut aliquip exea cojmm odo consequat. Duis aute irure dolor...</p>
</article>
<article class="service s3 abs">
  <div class="service-icon"><svg viewBox="0 0 90 90"><ellipse cx="45" cy="46" rx="17" ry="12" fill="#fff"/><rect x="34" y="54" width="5" height="7" fill="#fff"/><rect x="50" y="54" width="5" height="7" fill="#fff"/><rect x="60" y="42" width="5" height="6" fill="#fff"/><rect x="41" y="35" width="8" height="2" fill="#1c1c1c"/></svg></div>
  <h3>Superannuation</h3>
  <p class="lead">Lorem ipsuLorem ipsum dolor sit amet conse ct etur adipisicing elit, sed dom dolor.</p>
  <p class="body">Lorem ipsum dolor sit amet conse ctetur adipisicing elit, sed do eiusmod tempor incididunt ut labore et dolore magna aliqua. Ut enim ad minim venialkorwem, quis nostrud exercitation ullamco laboris nisi ut aliquip s nisi ut aliquip exea cojmm odo consequat. Duis aute irure dolor...</p>
</article>
<article class="service s4 abs">
  <div class="service-icon"><svg viewBox="0 0 90 90"><circle cx="41" cy="41" r="13" fill="none" stroke="#fff" stroke-width="4"/><circle cx="41" cy="41" r="8" fill="#fff"/><path d="M51 51 L62 62" stroke="#fff" stroke-width="6" stroke-linecap="round"/></svg></div>
  <h3>Audit</h3>
  <p class="lead">Lorem ipsuLorem ipsum dolor sit amet conse ct etur adipisicing elit, sed dom dolor.</p>
  <p class="body">Lorem ipsum dolor sit amet conse ctetur adipisicing elit, sed do eiusmod tempor incididunt ut labore et dolore magna aliqua. Ut enim ad minim venialkorwem, quis nostrud exercitation ullamco laboris nisi ut aliquip s nisi ut aliquip exea cojmm odo consequat. Duis aute irure dolor...</p>
</article>
<div class="btn-more abs">VIEW MORE</div>
<div class="divider abs"></div>

<h2 class="section-title news-title abs">Latest News</h2>
<div class="news-date abs" style="top:1558px"><b>14</b><span>JULY</span></div>
<p class="news-head abs" style="top:1558px">Aenean auctor wisi et urna</p>
<p class="news-by abs" style="top:1580px">Posted by Admin</p>
<div class="news-photo abs" style="top:1638px;background:linear-gradient(135deg,#2d5d97,#9cc4e8)" role="img" aria-label="Businessman standing in a blue tunnel"></div>
<p class="news-text abs" style="top:1632px">Maecenas mattis vitae tellus vel interdum. Quisque lacinia mauris id convallis pretium. Aliquam id odio sit amet mauris porttitor iaculis a eu dui.Maecenas mattis vitae tellus vel interdum. Quisque lacinia mauris id convallis pretium. Aliquam id odio sit amet mauris porttitor iaculis a eu dui.</p>
<div class="news-sep abs"></div>
<div class="news-date abs" style="top:1789px"><b>14</b><span>JULY</span></div>
<p class="news-head abs" style="top:1789px">Aenean auctor wisi et urna</p>
<p class="news-by abs" style="top:1811px">Posted by Admin</p>
<div class="news-photo abs" style="top:1869px;background:linear-gradient(135deg,#0f1c22,#3b6a72)" role="img" aria-label="Close-up of a man in a dark suit"></div>
<p class="news-text abs" style="top:1863px">Maecenas mattis vitae tellus vel interdum. Quisque lacinia mauris id convallis pretium. Aliquam id odio sit amet mauris porttitor iaculis a eu dui.Maecenas mattis vitae tellus vel interdum. Quisque lacinia mauris id convallis pretium. Aliquam id odio sit amet mauris porttitor iaculis a eu dui.</p>

<h2 class="section-title about-title abs">About Us</h2>
<p class="about-text abs">Maecenas mattis vitae tellus vel interdum. Quisque lacinia mauris id convallis pretium. Aliquam id odio sit amet mauris porttitor iaculis a eu dui.Maecenas mattis vitae tellus vel interdum. Quisque lacinia mauris id convallis pretium.</p>
<h2 class="section-title gallery-title abs">Our Gallery</h2>
<div class="gallery abs">
  <div role="img" aria-label="Business people on a city skyline"></div>
  <div role="img" aria-label="Businessman in a blue tunnel"></div>
  <div role="img" aria-label="Hand pointing with a magnifier"></div>
  <div class="wide" role="img" aria-label="Two businessmen reaching across a gap"></div>
  <div role="img" aria-label="Businessman portrait"></div>
  <div role="img" aria-label="Businessman standing on stacked coins"></div>
</div>

<section class="newsletter abs">
  <p>If you have fresh ideas, sign up for <em>our newsletter</em></p>
  <div class="field">Name:</div>
  <div class="subscribe">SUBSCRIBE</div>
</section>

<footer class="site-footer abs">
  <div class="foot-brand abs"><i></i>RK Donnelly &amp; Associates</div>
  <div class="socials abs"><span></span><span></span><span></span><span></span></div>
  <p class="copy abs">© 2014. All Rights Reserved. Privacy</p>
  <div class="foot-col col-posts abs">
    <h4>LATEST POSTS</h4>
    <div class="rule"></div>
    <p>Eos et accusamus et iustom odgnissi-mos ducimus qui blap.</p>
    <p class="ago">5 Days ago.</p>
    <div class="rule bottom"></div>
  </div>
  <div class="foot-col col-support abs">
    <h4>ONLINE SUPPORT</h4>
    <div class="phone">+ 8 800 555 21 64</div>
    <p>Ask Your questions by e-mail: <b>mail@rkdonnelly.org</b></p>
    <div class="rule"></div>
  </div>
  <div class="foot-col col-links abs">
    <h4>LINKS</h4>
    <ul><li>Home</li><li>Interiors</li><li>Expertise</li><li>Products</li></ul>
  </div>
</footer>

</body>
</html>
```